Falkrin homes and renovations business card design.

Would like some new card designs utilizing my new logo that look professional. I am open to different colors on the logo or utilize the same ones we have. I like the original concept but would like to see some fresh ideas and build on what we have already done.

Target Market(s)

Custom home building industry, Real estate sales, Renovation projects.

Industry/Entity Type

Home Builder

Contact Information for Business Card

Falkrin Homes and Renovations
2871 96th Avenue
Corvale, Northland
T2R3W8
Home : 403- 718-4063 Cell: 403- 294-5170

My info is : Dax Falkrin, President and CEO
email: falkrinhomes@maildrop-example.net
Website: falkrinhomes-example.com
websit

Requirements
Must have
• Must Use my new logo design. I am open to different colors on the logo or utilize the same ones in the existing design. I can upload the original logo design if needed.

```html
<!DOCTYPE html>
<html lang="en">
<head>
<meta charset="utf-8">
<title>Falkrin Homes and Renovations – Business Card</title>
<link href="https://fonts.googleapis.com/css2?family=Montserrat:wght@300;400;600&display=swap" rel="stylesheet">
<style>
  :root {
    --backdrop: #dcdcde;
    --charcoal: #3f3f41;
    --sunflower: #f7bb1e;
    --gold: #b8892b;
    --ink: #3f3f41;
  }
  html, body {
    margin: 0;
    width: 1200px;
    height: 800px;
    overflow: hidden;
    background: var(--backdrop);
    font-family: "Montserrat", Arial, sans-serif;
  }
  .canvas { position: relative; width: 1200px; height: 800px; }
  .card {
    position: absolute;
    left: 346px;
    width: 510px;
    height: 282px;
    border-radius: 14px;
    overflow: hidden;
  }
  .card--front { top: 70px; background: var(--sunflower); }
  .card--back { top: 410px; background: var(--charcoal); }
  .card__shapes { position: absolute; inset: 0; }

  .brand {
    position: absolute;
    text-align: center;
    color: var(--gold);
    font-weight: 600;
    line-height: 1.1;
  }
  .brand__name { display: block; }
  .brand__tag { display: block; }
  .card--front .brand { left: 0; width: 216px; top: 146px; }
  .card--front .brand__name { font-size: 31px; letter-spacing: 0.5px; }
  .card--front .brand__tag { font-size: 10px; letter-spacing: 0.2px; margin-top: 2px; }
  .card--back .brand { left: 0; width: 510px; top: 146px; }
  .card--back .brand__name { font-size: 46px; letter-spacing: 1px; }
  .card--back .brand__tag { font-size: 14.5px; letter-spacing: 0.3px; margin-top: 3px; }

  .holder {
    position: absolute;
    left: 282px;
    width: 210px;
    top: 16px;
    text-align: center;
    color: var(--ink);
  }
  .holder__name { font-size: 24px; font-weight: 400; line-height: 1; letter-spacing: 0.3px; }
  .holder__title { font-size: 12.5px; font-weight: 300; margin-top: 1px; }

  .contact {
    position: absolute;
    left: 295px;
    color: var(--ink);
    font-weight: 300;
    font-size: 14.5px;
    line-height: 17.5px;
    margin: 0;
    white-space: nowrap;
  }
  .contact--phone { top: 81px; }
  .contact--address { top: 125px; }
  .contact--email { top: 175px; font-size: 11px; }
  .contact--web { top: 213px; font-size: 12.5px; }
</style>
</head>
<body>
<main class="canvas">

  <section class="card card--front" aria-label="Business card front">
    <svg class="card__shapes" width="510" height="282" viewBox="0 0 510 282">
      <rect class="panel-dark" x="0" y="0" width="254" height="282" fill="var(--charcoal)"/>
      <rect class="divider" x="254" y="0" width="5" height="54" fill="var(--sunflower)"/>
      <rect class="divider" x="254" y="262" width="5" height="20" fill="var(--sunflower)"/>
      <rect class="divider-edge" x="259" y="0" width="4" height="54" fill="var(--charcoal)"/>
      <rect class="divider-edge" x="259" y="262" width="4" height="20" fill="var(--charcoal)"/>
      <polygon class="icon-tab" points="250,54 266,54 283,78 283,238 266,262 250,262 234,238 234,78" fill="var(--charcoal)" stroke="var(--sunflower)" stroke-width="1.5"/>

      <g class="icon icon--phone">
        <circle cx="256" cy="100" r="14" fill="var(--charcoal)" stroke="var(--sunflower)" stroke-width="1.2"/>
        <rect x="251.5" y="92" width="9" height="16" rx="1.5" fill="none" stroke="var(--sunflower)" stroke-width="1.3"/>
        <line x1="254.5" y1="105.5" x2="257.5" y2="105.5" stroke="var(--sunflower)" stroke-width="1.1"/>
      </g>
      <g class="icon icon--pin">
        <circle cx="256" cy="142" r="14" fill="var(--charcoal)" stroke="var(--sunflower)" stroke-width="1.2"/>
        <path d="M256 152 C251 145 249.5 142 249.5 139.5 A6.5 6.5 0 0 1 262.5 139.5 C262.5 142 261 145 256 152 Z" fill="var(--sunflower)"/>
        <circle cx="256" cy="139.5" r="2.3" fill="var(--charcoal)"/>
      </g>
      <g class="icon icon--mail">
        <circle cx="256" cy="182" r="14" fill="var(--charcoal)" stroke="var(--sunflower)" stroke-width="1.2"/>
        <rect x="247.5" y="176" width="17" height="12" fill="none" stroke="var(--sunflower)" stroke-width="1.3"/>
        <polyline points="247.5,176 256,183 264.5,176" fill="none" stroke="var(--sunflower)" stroke-width="1.3"/>
      </g>
      <g class="icon icon--web">
        <circle cx="256" cy="221" r="14" fill="var(--charcoal)" stroke="var(--sunflower)" stroke-width="1.2"/>
        <circle cx="256" cy="221" r="8" fill="none" stroke="var(--sunflower)" stroke-width="1.2"/>
        <ellipse cx="256" cy="221" rx="3.5" ry="8" fill="none" stroke="var(--sunflower)" stroke-width="1"/>
        <line x1="248" y1="221" x2="264" y2="221" stroke="var(--sunflower)" stroke-width="1"/>
      </g>
    </svg>

    <div class="brand">
      <span class="brand__name">FALKRIN</span>
      <span class="brand__tag">HOMES AND RENOVATIONS</span>
    </div>

    <div class="holder">
      <div class="holder__name">Dax Falkrin</div>
      <div class="holder__title">President and CEO</div>
    </div>

    <p class="contact contact--phone">403- 718-4063<br>403- 294-5170</p>
    <p class="contact contact--address">2871 96th Avenue<br>Corvale, Northland</p>
    <p class="contact contact--email">falkrinhomes@maildrop-example.net</p>
    <p class="contact contact--web">www.falkrinhomes-example.com</p>
  </section>

  <section class="card card--back" aria-label="Business card back">
    <div class="brand">
      <span class="brand__name">FALKRIN</span>
      <span class="brand__tag">HOMES AND RENOVATIONS</span>
    </div>
  </section>

</main>
</body>
</html>
```